Business Card Design for company

We want new business cards. We'd like something different-- yet still highly professional. Our tagline is Providing leadership, delivering success. Stock photos are ok, as long as they are relevant and look upscale.

Target Market(s)

Architecture/Business Management Consulting/Engineering Consulting

Contact Information for Business Card

dark gray background with pops of blue might be good, but you tell me. You're the designers. Rounded corners might be nice, but again, you tell me.

Font styles to use
Serif
Sans Serif

Colors
3276b5
5c5c5c
9d9d9d
fbfbfb

Requirements
Nice to have
• Something different, but still very professional.

```html
<!DOCTYPE html>
<html lang="en">
<head>
<meta charset="utf-8">
<title>Veltran Group – Business Cards</title>
<link rel="stylesheet" href="https://fonts.googleapis.com/css2?family=Open+Sans:wght@300;400;600&display=swap">
<style>
  :root {
    --brand-blue: #3276b5;
    --brand-blue-light: #3f8ad0;
    --brand-blue-dark: #225b94;
    --ink-gray: #5c5c5c;
    --soft-gray: #9d9d9d;
    --paper: #fbfbfb;
    --stage: #e6e7ea;
  }
  * { box-sizing: border-box; margin: 0; padding: 0; }
  html, body {
    width: 1200px;
    height: 900px;
    overflow: hidden;
    background: var(--stage);
    font-family: "Open Sans", Arial, sans-serif;
  }
  .sheet {
    width: 1200px;
    height: 900px;
    display: flex;
    align-items: center;
    justify-content: center;
    gap: 44px;
  }
  .card {
    position: relative;
    width: 540px;
    height: 309px;
    border-radius: 26px;
    overflow: hidden;
    box-shadow: 0 10px 28px rgba(0,0,0,0.18);
  }

  /* Front */
  .card-front {
    background: linear-gradient(160deg, var(--brand-blue-light) 0%, var(--brand-blue) 55%, var(--brand-blue-dark) 100%);
    color: var(--paper);
  }
  .world-map-area {
    position: absolute;
    inset: 24px 30px;
    border-radius: 40%;
    background: radial-gradient(ellipse at 50% 50%, rgba(120,180,235,0.35) 0%, rgba(120,180,235,0.12) 55%, rgba(120,180,235,0) 75%);
  }
  .brand-block {
    position: absolute;
    inset: 0;
    display: flex;
    flex-direction: column;
    align-items: center;
    justify-content: center;
    gap: 22px;
  }
  .brand-name {
    font-weight: 300;
    font-size: 44px;
    letter-spacing: 3px;
    color: var(--paper);
    text-transform: uppercase;
  }
  .tagline {
    font-weight: 400;
    font-size: 11px;
    letter-spacing: 1.6px;
    text-transform: uppercase;
    color: var(--paper);
  }

  /* Back */
  .card-back { background: var(--paper); }
  .back-wave { position: absolute; inset: 0; }
  .identity {
    position: absolute;
    right: 256px;
    top: 42px;
    text-align: right;
  }
  .person-name {
    font-size: 19px;
    font-weight: 400;
    letter-spacing: 0.5px;
    color: var(--brand-blue);
    text-transform: uppercase;
    white-space: nowrap;
  }
  .person-role {
    margin-top: 2px;
    font-size: 13px;
    color: var(--soft-gray);
    white-space: nowrap;
  }
  .divider {
    position: absolute;
    left: 300px;
    top: 30px;
    width: 1px;
    height: 180px;
    background: var(--brand-blue);
  }
  .contact-list {
    position: absolute;
    left: 316px;
    top: 36px;
    list-style: none;
    font-size: 11.5px;
    line-height: 1.45;
    color: var(--ink-gray);
  }
  .contact-item {
    display: flex;
    gap: 7px;
    margin-bottom: 6px;
  }
  .contact-icon {
    flex: 0 0 11px;
    width: 11px;
    height: 11px;
    margin-top: 3px;
    fill: var(--brand-blue);
  }
</style>
</head>
<body>
<main class="sheet">

  <section class="card card-front" aria-label="Card front">
    <div class="world-map-area" role="img" aria-label="Faint dotted world map in light blue"></div>
    <div class="brand-block">
      <h1 class="brand-name">Veltran Group</h1>
      <p class="tagline">Guiding strategy | Building results</p>
    </div>
  </section>

  <section class="card card-back" aria-label="Card back">
    <svg class="back-wave" viewBox="0 0 540 309" preserveAspectRatio="none" aria-hidden="true">
      <path d="M0 86 C 80 110, 150 170, 190 250 C 205 285, 230 305, 260 309 L 0 309 Z" fill="var(--soft-gray)" opacity="0.55"/>
      <path d="M0 96 C 75 120, 140 180, 178 258 C 192 288, 212 305, 236 309 L 0 309 Z" fill="var(--brand-blue)"/>
    </svg>

    <div class="identity">
      <h2 class="person-name">Owen Hartley</h2>
      <p class="person-role">Design Consultant</p>
    </div>

    <div class="divider"></div>

    <ul class="contact-list">
      <li class="contact-item">
        <svg class="contact-icon" viewBox="0 0 12 12" aria-hidden="true"><path d="M3 1 L5 3.5 L4 4.8 C4.8 6.4 5.8 7.4 7.2 8 L8.5 7 L11 9 L9.8 11 C5.5 10.6 1.4 6.5 1 2.2 Z"/></svg>
        <span>01632 960418 (Ashford)<br>01632 960774 (Millbrook)<br>555-201-4836</span>
      </li>
      <li class="contact-item">
        <svg class="contact-icon" viewBox="0 0 12 12" aria-hidden="true"><path d="M1 3 H11 V10 H1 Z M1.6 3.4 L6 7 L10.4 3.4" fill="none" stroke="var(--brand-blue)" stroke-width="1.1"/></svg>
        <span>info@veltrangroup.com</span>
      </li>
      <li class="contact-item">
        <svg class="contact-icon" viewBox="0 0 12 12" aria-hidden="true"><path d="M6 0.8 C3.8 0.8 2.2 2.4 2.2 4.5 C2.2 7.2 6 11.2 6 11.2 C6 11.2 9.8 7.2 9.8 4.5 C9.8 2.4 8.2 0.8 6 0.8 Z M6 3 A1.5 1.5 0 1 0 6 6 A1.5 1.5 0 1 0 6 3 Z" fill-rule="evenodd"/></svg>
        <span>Unit 8, The Fenwick Centre,<br>Millbrook Park, Ashford,<br>Kent TN9 4QL</span>
      </li>
      <li class="contact-item">
        <svg class="contact-icon" viewBox="0 0 12 12" aria-hidden="true"><g fill="none" stroke="var(--brand-blue)" stroke-width="1"><circle cx="6" cy="6" r="5"/><ellipse cx="6" cy="6" rx="2.2" ry="5"/><path d="M1 6 H11"/></g></svg>
        <span>veltrangroup.com</span>
      </li>
    </ul>
  </section>

</main>
</body>
</html>
```